Card Design for my dog training business Brightpaw Obedience

Need a business card design for my dog training business with my new logo. Want the card to come off professional yet fun. Want it to be very eye catchy as well. I normally have these at vet clinics, pet stores, and groomers. so need it to look better than my competitors.
Target Market(s)
dog owners
Industry/Entity Type
Dog Training
Contact Information for Business Card
needs logo, my name and info
Font styles to use
Serif
Colors
0255a3
ffffff
ec1f27
000000
333333
fbfbfb
Requirements
Must have
- Brightpaw Obedience
- Felix Orland
- 415 903 2276
- info@brightpawobedience.example
- www.brightpawobedience.example

```html
<!DOCTYPE html>
<html lang="en">
<head>
<meta charset="utf-8">
<title>Brightpaw Obedience — Business Card</title>
<link href="https://fonts.googleapis.com/css2?family=EB+Garamond:ital,wght@0,500;1,400&family=Open+Sans:wght@400;700&display=swap" rel="stylesheet">
<style>
  :root {
    --backdrop: #4a3f3a;
    --card-dark: #16181b;
    --card-light: #ffffff;
    --ink: #000000;
    --ink-soft: #333333;
    --silver: #b9bcc0;
    --divider: #c9c9c9;
  }
  * { box-sizing: border-box; margin: 0; padding: 0; }
  html, body { width: 1200px; height: 864px; overflow: hidden; }
  body {
    background: var(--backdrop);
    position: relative;
    font-family: "Open Sans", sans-serif;
  }
  .card {
    position: absolute;
    left: 285px;
    width: 630px;
    height: 360px;
    border-radius: 2px;
    box-shadow: 0 6px 18px rgba(0,0,0,0.35);
  }
  /* Back of card */
  .card-back {
    top: 48px;
    background: var(--card-dark);
    display: flex;
    flex-direction: column;
    align-items: center;
    justify-content: center;
    gap: 26px;
  }
  .brand-name {
    font-family: "EB Garamond", serif;
    font-weight: 500;
    letter-spacing: 0.02em;
  }
  .card-back .brand-name {
    color: var(--silver);
    font-size: 40px;
  }
  .tagline {
    font-family: "EB Garamond", serif;
    font-style: italic;
    font-size: 20px;
    color: var(--silver);
  }
  /* Front of card */
  .card-front {
    top: 456px;
    background: var(--card-light);
    display: flex;
    align-items: center;
    padding: 0 40px 0 36px;
  }
  .brand-block {
    width: 210px;
    flex: none;
    text-align: center;
  }
  .card-front .brand-name {
    color: var(--ink);
    font-size: 28px;
    line-height: 1.1;
  }
  .divider {
    width: 1px;
    height: 150px;
    flex: none;
    background: var(--divider);
    margin: 0 32px;
  }
  .contact { min-width: 0; }
  .contact-name {
    font-weight: 700;
    font-size: 24px;
    color: var(--ink);
    margin-bottom: 12px;
  }
  .contact-list { list-style: none; }
  .contact-list li {
    display: flex;
    align-items: center;
    gap: 10px;
    font-size: 16px;
    color: var(--ink-soft);
    line-height: 1.55;
    white-space: nowrap;
  }
  .contact-list svg { width: 14px; height: 14px; fill: var(--ink-soft); flex: none; }
</style>
</head>
<body>
  <section class="card card-back">
    <div class="brand-name">Brightpaw Obedience</div>
    <p class="tagline">“Teaching good manners one happy dog at a time.”</p>
  </section>

  <section class="card card-front">
    <div class="brand-block">
      <div class="brand-name">Brightpaw<br>Obedience</div>
    </div>
    <div class="divider"></div>
    <div class="contact">
      <h1 class="contact-name">Felix Orland</h1>
      <ul class="contact-list">
        <li>
          <svg viewBox="0 0 16 16" aria-hidden="true"><path d="M3 1h3l1.5 4-2 1.3a9 9 0 0 0 4.2 4.2L11 8.5l4 1.5v3a2 2 0 0 1-2 2A12 12 0 0 1 1 3a2 2 0 0 1 2-2z"/></svg>
          415 903 2276
        </li>
        <li>
          <svg viewBox="0 0 16 16" aria-hidden="true"><path d="M1 3h14v10H1z M1 3l7 6 7-6" fill="none" stroke="#333333" stroke-width="1.6"/></svg>
          info@brightpawobedience.example
        </li>
        <li>
          <svg viewBox="0 0 16 16" aria-hidden="true"><circle cx="8" cy="8" r="7"/><path d="M8 1v14M1 8h14" stroke="#fff" stroke-width="1.2"/></svg>
          www.brightpawobedience.example
        </li>
      </ul>
    </div>
  </section>
</body>
</html>
```